New Webpage for High Class Expert Witness Services Company

We are looking for a minimalist design for a webpage that just has our logo and an entry form offer to connect with one of our Liaisons.
The entry form should just ask for Name, Email, Contact Info and Description of Project.

Company Name is: The Marlowe Crest Advisory Services

Number of Pages Required

1 page

```html
<!DOCTYPE html>
<html lang="en">
<head>
<meta charset="utf-8">
<title>The Marlowe Crest Advisory Services — Connect with a Liaison</title>
<link rel="stylesheet" href="https://fonts.googleapis.com/css2?family=Cinzel:wght@400&family=Montserrat:wght@400&display=swap">
<style>
  :root {
    --bg: #000000;
    --ink: #ffffff;
    --ink-soft: #d9d9d9;
    --gold-glow: rgba(168, 134, 72, 0.32);
    --gold-faint: rgba(168, 134, 72, 0.12);
    --field-border: #e6e6e6;
    --button-top: #3a3a3a;
    --button-bottom: #050505;
    --rule: #333333;
  }
  * { box-sizing: border-box; margin: 0; padding: 0; }
  html, body { width: 823px; height: 1200px; overflow: hidden; background: var(--bg); }
  body { position: relative; font-family: "Montserrat", sans-serif; color: var(--ink); }

  .backdrop { position: absolute; pointer-events: none; }
  .backdrop--top {
    left: 0; top: 0; width: 823px; height: 230px;
    background:
      radial-gradient(ellipse 120px 200px at 20px 40px, var(--gold-glow), transparent 70%),
      radial-gradient(ellipse 140px 180px at 700px 20px, var(--gold-glow), transparent 70%),
      radial-gradient(ellipse 300px 160px at 410px 0, var(--gold-faint), transparent 70%);
  }
  .backdrop--bottom {
    left: 0; bottom: 0; width: 823px; height: 240px;
    background:
      radial-gradient(ellipse 200px 180px at 760px 240px, var(--gold-glow), transparent 70%),
      radial-gradient(ellipse 260px 120px at 400px 240px, var(--gold-faint), transparent 70%);
  }

  .brand {
    position: absolute; left: 0; width: 823px; top: 84px;
    display: flex; justify-content: center; align-items: center; gap: 10px;
  }
  .brand-mark { width: 14px; height: 14px; border-radius: 50%; background: var(--ink-soft); }
  .brand-name { font-family: "Cinzel", serif; font-size: 20px; letter-spacing: 1px; color: var(--ink-soft); }

  .center { position: absolute; left: 0; width: 823px; text-align: center; }
  .hero-title { top: 156px; font-family: "Cinzel", serif; font-size: 33px; font-weight: 400; color: #eeeeee; letter-spacing: 0.5px; }
  .hero-lead { top: 212px; font-size: 12px; line-height: 19.5px; color: var(--ink-soft); }

  .btn {
    position: absolute; height: 39px; width: 212px;
    border: 1px solid #8a8a8a; border-radius: 7px;
    background: linear-gradient(var(--button-top), var(--button-bottom));
    color: #eeeeee; font-family: "Montserrat", sans-serif; font-size: 13px;
    letter-spacing: 0.2px; text-transform: uppercase;
    display: flex; align-items: center; justify-content: center;
  }
  .btn--hero { left: 305px; top: 276px; }
  .btn--submit { left: 307px; top: 992px; }

  .section-title { top: 376px; font-family: "Cinzel", serif; font-size: 34px; font-weight: 400; color: #eeeeee; }
  .section-lead { top: 436px; left: 80px; width: 663px; font-size: 12.4px; line-height: 19.5px; color: var(--ink-soft); }

  .field-label { position: absolute; left: 161px; font-size: 13px; color: #e8e8e8; }
  .field {
    position: absolute; left: 161px; width: 503px; height: 38px;
    border: 1px solid var(--field-border); border-radius: 7px; background: var(--bg);
  }
  .field--area { height: 120px; }

  .footer-rule { position: absolute; left: 0; top: 1114px; width: 823px; height: 1px; background: var(--rule); }
  .footer-note { top: 1130px; font-size: 11px; color: #e8e8e8; }
</style>
</head>
<body>
  <div class="backdrop backdrop--top" role="img" aria-label="Fine gold line pattern on black"></div>
  <div class="backdrop backdrop--bottom" role="img" aria-label="Fine gold line pattern on black"></div>

  <header class="brand">
    <span class="brand-mark"></span>
    <span class="brand-name">Marlowe Crest Advisory Services</span>
  </header>

  <h1 class="center hero-title">Discreet. Precise. Reliable.</h1>
  <p class="center hero-lead">Connecting legal teams with elite medical experts<br>—efficiently and confidentially.</p>
  <div class="btn btn--hero">Connect with a Liaison</div>

  <h2 class="center section-title">Connect with a Liaison Today</h2>
  <p class="center section-lead">Submit your request below and a dedicated liaison will respond promptly to understand your case needs and coordinate the right expert support.</p>

  <form class="liaison-form">
    <label class="field-label" style="top:503px">Full Name</label>
    <div class="field" style="top:535px"></div>
    <label class="field-label" style="top:601px">Email Address</label>
    <div class="field" style="top:633px"></div>
    <label class="field-label" style="top:699px">Contact Information</label>
    <div class="field" style="top:731px"></div>
    <label class="field-label" style="top:797px">Project Description</label>
    <div class="field field--area" style="top:828px"></div>
    <div class="btn btn--submit">Submit Request</div>
  </form>

  <div class="footer-rule"></div>
  <p class="center footer-note">© The Marlowe Crest Advisory Services All Rights Reserved</p>
</body>
</html>
```